Reach Crafters Unique Marketing Website Design

I am starting a new company that is a thought leader in the marketing consulting space. The company is called Reach Crafters. We intend to build a Wordpress site on the Astra Theme with the Spectra builder. Our goal is to become the leading voice that empowers high-ticket service business leaders to become Reach Crafters by equipping them with the cutting-edge frameworks and decision grade intelligence taught in leading business schools. What we are looking for is a website design that is clean and professional, making some use of white space well also being eye catching and distinctive in the consulting space. We will probably want to have a video on the homepage not in the hero section, but just below to explain the company and what we do. Our tagline is "Be found. Be chosen." I have attached a brand guide with some messaging, our typography choices, and our color system. The full site will have a primary nav that is four pages - About us, Services, Insights (essentially a blog), and Contact Us. The goal of this project is to develop an art direction that I can give to a designer to build loads of new pages.

Target Market(s)

Business owners (mostly male) from 30-60 years old, looking to fix their sales and marketing funnel.

Industry/Entity Type

Marketing consulting

Font styles to use
Sans Serif

Requirements
Must have
• A clean, professional design that builds trust with owners of high-ticket service businesses. We need a space for explainer video, and sections that tell prospects what we do. Would also like to have a blog carousel.
Nice to have
• Social feeds, if possible. See attached documents for colors and fonts.
Should not have
• Our feel is professional enough to be trustworthy, but unique enough to be memorable. Cartoon ideas do not meet the professional test, and we do not want the website to appear feminine.

```html
<!DOCTYPE html>
<html lang="en">
<head>
<meta charset="utf-8">
<title>Reach Crafters — Be found. Be chosen.</title>
<link href="https://fonts.googleapis.com/css2?family=Oswald:wght@400;500;600;700&family=Poppins:ital,wght@0,400;0,500;0,600;1,400&display=swap" rel="stylesheet">
<style>
:root{
  --ink:#0c1526;
  --text:#333333;
  --muted:#555555;
  --green:#17b47c;
  --blue:#3152f5;
  --link-blue:#3b5bdb;
  --charcoal:#2f2f2f;
  --soft:#f2f2f2;
  --white:#ffffff;
  --head:'Oswald',sans-serif;
  --body:'Poppins',sans-serif;
}
*{margin:0;padding:0;box-sizing:border-box}
html,body{width:1200px;height:3976px;overflow:hidden}
body{position:relative;background:var(--white);font-family:var(--body);color:var(--text)}
.abs{position:absolute}
.btn{position:absolute;display:flex;align-items:center;justify-content:center;font-family:var(--head);font-weight:500;font-size:20px;color:var(--white);border-radius:6px;letter-spacing:.3px}
.btn--dark{background:var(--ink)}
.btn--green{background:var(--green)}
.section-title{position:absolute;font-family:var(--head);font-size:38px;font-weight:400;color:var(--text);letter-spacing:.2px}
.section-title b{font-weight:700}

/* header */
.site-header{position:absolute;left:0;top:0;width:1200px;height:82px;background:var(--white)}
.brand{position:absolute;left:74px;top:24px;font-family:var(--head);font-weight:600;font-size:28px;color:var(--ink);letter-spacing:.3px}
.nav{position:absolute;top:33px;font-family:var(--head);font-size:16px;color:var(--text)}
.nav--active{color:var(--link-blue)}

/* hero */
.hero{position:absolute;left:0;top:82px;width:1200px;height:639px;background:
  linear-gradient(120deg,rgba(220,60,40,0) 62%,rgba(235,70,40,.55) 70%,rgba(220,60,40,0) 76%),
  linear-gradient(135deg,#06101e 0%,#0d2236 35%,#1c4a6e 55%,#1a2230 75%,#0a0f18 100%)}
.hero__kicker{position:absolute;left:74px;top:265px;font-family:var(--head);font-weight:600;font-size:60px;line-height:1;color:var(--white)}
.hero__title{position:absolute;left:74px;top:318px;font-family:var(--head);font-weight:600;font-size:80px;line-height:1;color:var(--white)}
.hero__tagline{position:absolute;left:74px;top:404px;font-family:var(--body);font-weight:500;font-size:34px;color:var(--white)}

/* about */
.about-band{position:absolute;left:0;top:0;width:1200px;height:3976px;pointer-events:none}
.about__lead{position:absolute;left:150px;top:838px;width:900px;text-align:center;font-size:17px;line-height:27px;color:var(--muted)}
.video{position:absolute;left:208px;top:920px;width:782px;height:385px;border-radius:6px;background:linear-gradient(120deg,#3a3f48 0%,#8e949c 40%,#c9ccd0 60%,#5a5f66 100%)}

/* services */
.arrow{position:absolute}
.card{position:absolute;top:1551px;width:243px;height:224px;background:var(--white);border-radius:6px}
.card--active{background:var(--ink)}
.card__icon{position:absolute;left:15px;top:15px;width:60px;height:60px;border-radius:8px;background:#ececef;display:flex;align-items:center;justify-content:center}
.card--active .card__icon{background:var(--green)}
.card__title{position:absolute;left:15px;top:89px;width:220px;font-size:19px;line-height:26px;font-weight:500;color:var(--ink)}
.card--active .card__title{color:var(--white)}
.card__more{position:absolute;left:15px;top:176px;height:32px;padding:0 13px;border:1.5px solid var(--green);border-radius:16px;font-size:11px;line-height:29px;color:var(--green);font-weight:500}
.card--active .card__more{color:var(--white)}

/* testimonials */
.testimonials{position:absolute;left:0;top:1940px;width:1200px;height:428px;background:var(--charcoal)}
.testimonials .section-title{color:var(--white)}
.quote{position:absolute;left:200px;top:133px;width:800px;text-align:center;font-style:italic;font-size:20px;line-height:34px;color:var(--white)}
.quote__name{position:absolute;left:0;top:259px;width:1200px;text-align:center;font-family:var(--head);font-weight:500;font-size:18px;color:var(--green)}
.dot{position:absolute;top:343px;width:11px;height:11px;border-radius:50%;background:var(--white)}
.dot--on{background:#8b6cf6}

/* news */
.post{position:absolute;top:2513px;width:513px;height:445px;border-radius:16px;overflow:hidden}
.post--a{left:74px;background:linear-gradient(120deg,#0f2a4a 0%,#2c6aa8 40%,#9fd0ee 65%,#3c4f63 100%)}
.post--b{left:613px;background:linear-gradient(120deg,#5f8ea6 0%,#a8cdda 45%,#c9d6d8 65%,#5e6a6c 100%)}
.post__caption{position:absolute;left:0;bottom:0;width:100%;height:112px;background:rgba(10,14,22,.82);padding:20px 24px 0}
.post__date{font-family:var(--head);font-size:15px;color:var(--green);font-weight:500}
.post__title{margin-top:6px;font-family:var(--head);font-size:19px;line-height:27px;color:var(--white);font-weight:500}

/* contact */
.address{position:absolute;left:74px;top:3209px;width:329px;height:357px;background:var(--blue);border-radius:16px;color:var(--white)}
.address__title{position:absolute;left:29px;top:38px;font-family:var(--head);font-size:21px;font-weight:500}
.address__row{position:absolute;left:29px;display:flex;gap:18px;font-size:14px;line-height:23px}
.address__row svg{flex:none;margin-top:2px}
.field{position:absolute;background:var(--white);border-radius:8px;font-size:13px;color:var(--text);padding:17px 17px}

/* footer */
.footer{position:absolute;left:0;top:3645px;width:1200px;height:331px;background:var(--charcoal);color:var(--white)}
.footer__brand{position:absolute;left:74px;top:92px;font-family:var(--head);font-weight:600;font-size:34px;letter-spacing:.3px}
.footer__copy{position:absolute;left:74px;top:152px;font-size:12px;line-height:23px}
.social{position:absolute;top:220px;width:22px;height:22px;border-radius:50%;border:2px solid var(--white)}
.footer__col{position:absolute;top:76px}
.footer__col h4{font-family:var(--head);font-size:20px;font-weight:500;margin-bottom:11px}
.footer__col li{list-style:none;font-size:15px;line-height:34px}
</style>
</head>
<body>

<header class="site-header">
  <div class="brand">REACH CRAFTERS</div>
  <nav>
    <span class="nav nav--active" style="left:683px">HOME</span>
    <span class="nav" style="left:755px">ABOUT US</span>
    <span class="nav" style="left:856px">SERVICES</span>
    <span class="nav" style="left:951px">INSIGHTS</span>
    <span class="nav" style="left:1047px">CONTACT US</span>
  </nav>
</header>

<section class="hero" role="img" aria-label="Confident business team standing with arms crossed under blue and red light streaks">
</section>
<div class="hero__kicker">WELCOME TO</div>
<div class="hero__title">REACH CRAFTERS</div>
<div class="hero__tagline">Be found. Be chosen.</div>
<div class="btn btn--green" style="left:74px;top:469px;width:185px;height:59px">LEARN MORE</div>

<!-- soft grey angled bands -->
<svg class="about-band" width="1200" height="3976" viewBox="0 0 1200 3976">
  <polygon points="1200,942 1200,1940 0,1940 0,1297" fill="#f2f2f2"/>
  <polygon points="0,3073 1200,2880 1200,3645 0,3645" fill="#f2f2f2"/>
</svg>

<section class="about">
  <h2 class="section-title" style="left:0;width:1200px;text-align:center;top:778px"><b>ABOUT</b> COMPANY</h2>
  <p class="about__lead">Discover how Reach Crafters use structured thinking, data-driven decisions, and proven frameworks to consistently attract and convert premium clients.</p>
  <div class="video" role="img" aria-label="Explainer video still: consultant presenting a chart to a team in a meeting room"></div>
  <svg class="abs" style="left:560px;top:1073px" width="78" height="78" viewBox="0 0 78 78">
    <circle cx="39" cy="39" r="35" fill="none" stroke="#fff" stroke-width="6"/>
    <polygon points="31,23 31,55 56,39" fill="#fff"/>
  </svg>
  <div class="btn btn--dark" style="left:434px;top:1340px;width:332px;height:59px">LEARN MORE ABOUT US</div>
</section>

<section class="services">
  <h2 class="section-title" style="left:74px;top:1478px"><b>OUR</b> SERVICES</h2>
  <svg class="arrow" style="left:1065px;top:1492px" width="20" height="26" viewBox="0 0 20 26"><polyline points="15,2 4,13 15,24" fill="none" stroke="#333" stroke-width="2.5"/></svg>
  <svg class="arrow" style="left:1108px;top:1492px" width="20" height="26" viewBox="0 0 20 26"><polyline points="5,2 16,13 5,24" fill="none" stroke="#17b47c" stroke-width="2.5"/></svg>

  <div class="card" style="left:74px">
    <div class="card__icon"><svg width="26" height="30" viewBox="0 0 26 30"><path d="M3 2h13l7 7v19H3z" fill="none" stroke="#0c1526" stroke-width="2.2"/><line x1="8" y1="14" x2="18" y2="14" stroke="#0c1526" stroke-width="2"/><line x1="8" y1="19" x2="18" y2="19" stroke="#0c1526" stroke-width="2"/><line x1="8" y1="24" x2="15" y2="24" stroke="#0c1526" stroke-width="2"/></svg></div>
    <div class="card__title">Demand Strategy &amp; Positioning</div>
    <div class="card__more">Learn More</div>
  </div>
  <div class="card card--active" style="left:344px">
    <div class="card__icon"><svg width="32" height="30" viewBox="0 0 32 30"><path d="M4 5h17a3 3 0 0 1 3 3v8a3 3 0 0 1-3 3H11l-5 4v-4H4a2 2 0 0 1-2-2V7a2 2 0 0 1 2-2z" fill="none" stroke="#fff" stroke-width="2.2"/><path d="M26 11h2a2 2 0 0 1 2 2v8a2 2 0 0 1-2 2h-1v4l-5-4h-7" fill="none" stroke="#fff" stroke-width="2.2"/></svg></div>
    <div class="card__title">High-Ticket Growth Consulting</div>
    <div class="card__more">Learn More</div>
  </div>
  <div class="card" style="left:615px">
    <div class="card__icon"><svg width="30" height="26" viewBox="0 0 30 26"><polyline points="3,2 3,23 28,23" fill="none" stroke="#0c1526" stroke-width="2.2"/><line x1="9" y1="19" x2="9" y2="11" stroke="#0c1526" stroke-width="2.4"/><line x1="14" y1="19" x2="14" y2="7" stroke="#0c1526" stroke-width="2.4"/><line x1="19" y1="19" x2="19" y2="13" stroke="#0c1526" stroke-width="2.4"/><line x1="24" y1="19" x2="24" y2="5" stroke="#0c1526" stroke-width="2.4"/></svg></div>
    <div class="card__title">Decision Intelligence &amp; Analytics</div>
    <div class="card__more">Learn More</div>
  </div>
  <div class="card" style="left:885px">
    <div class="card__icon"><svg width="32" height="26" viewBox="0 0 32 26"><rect x="5" y="3" width="22" height="15" rx="1.5" fill="none" stroke="#0c1526" stroke-width="2.4"/><rect x="1" y="19" width="30" height="4" rx="1.5" fill="#0c1526"/></svg></div>
    <div class="card__title">Leadership &amp; Market Insight Workshops</div>
    <div class="card__more">Learn More</div>
  </div>

  <div class="btn btn--dark" style="left:479px;top:1821px;width:242px;height:59px">VIEW ALL SERVICES</div>
</section>

<section class="testimonials">
  <h2 class="section-title" style="left:0;width:1200px;text-align:center;top:60px"><b>OUR</b> TESTIMONIALS</h2>
  <p class="quote">“ Nemo enim ipsam voluptatem quia voluptas sit aspernatur aut odit aut fugit, sed quia consequuntur magni dolores eos qui ratione voluptatem sequi nesciunt...”</p>
  <div class="quote__name">NAME HEADING</div>
  <span class="dot dot--on" style="left:561px"></span>
  <span class="dot" style="left:584px"></span>
  <span class="dot" style="left:607px"></span>
  <span class="dot" style="left:630px"></span>
</section>

<section class="news">
  <h2 class="section-title" style="left:0;width:1200px;text-align:center;top:2418px"><b>NEWS</b> INSIGHTS</h2>
  <svg class="arrow" style="left:43px;top:2720px" width="20" height="28" viewBox="0 0 20 28"><polyline points="15,2 4,14 15,26" fill="none" stroke="#333" stroke-width="2.5"/></svg>
  <svg class="arrow" style="left:1138px;top:2720px" width="20" height="28" viewBox="0 0 20 28"><polyline points="5,2 16,14 5,26" fill="none" stroke="#333" stroke-width="2.5"/></svg>
  <article class="post post--a" role="img" aria-label="Analyst presenting dashboards on a large curved screen">
    <div class="post__caption">
      <div class="post__date">JAN 28, 2025</div>
      <div class="post__title">DUIS AUTE IRURE DOLOR IN REPREHENDERIT IN VOLUPTATE VELIT ESSE CILLUM DOLORE..</div>
    </div>
  </article>
  <article class="post post--b" role="img" aria-label="Support agent with headset beside a floating ticket-metrics panel">
    <div class="post__caption">
      <div class="post__date">JAN 28, 2025</div>
      <div class="post__title">DUIS AUTE IRURE DOLOR IN REPREHENDERIT IN VOLUPTATE VELIT ESSE CILLUM DOLORE..</div>
    </div>
  </article>
  <div class="btn btn--dark" style="left:479px;top:3016px;width:242px;height:59px">VIEW ALL BLOG</div>
</section>

<section class="contact">
  <h2 class="section-title" style="left:74px;top:3133px"><b>CONTACT</b> US</h2>
  <div class="address">
    <div class="address__title">ADDRESS INFO</div>
    <div class="address__row" style="top:88px">
      <svg width="26" height="22" viewBox="0 0 26 22"><path d="M1 4l7-3 9 3 8-3v17l-8 3-9-3-7 3z" fill="#fff"/><line x1="8" y1="1" x2="8" y2="18" stroke="#3152f5" stroke-width="1.5"/><line x1="17" y1="4" x2="17" y2="21" stroke="#3152f5" stroke-width="1.5"/></svg>
      <span>48 Harbor Lane Suite 210,<br>Boston 02110, United States</span>
    </div>
    <div class="address__row" style="top:160px">
      <svg width="26" height="22" viewBox="0 0 26 22"><path d="M6 1l4 5-2.5 2.5c1.5 3 3.5 5 6.5 6.5L16.5 12l5 4-2.5 4c-8 0-16-8-16-16z" fill="#fff"/></svg>
      <span>+1-555-010-2040</span>
    </div>
    <div class="address__row" style="top:208px">
      <svg width="26" height="22" viewBox="0 0 26 22"><rect x="2" y="3" width="22" height="15" rx="2" fill="#fff"/><polyline points="3,5 13,12 23,5" fill="none" stroke="#3152f5" stroke-width="1.8"/></svg>
      <span>hello@reachcrafters.example</span>
    </div>
    <div class="btn btn--green" style="left:29px;top:259px;width:241px;height:59px">GET DIRECTION</div>
  </div>

  <div class="field" style="left:525px;top:3209px;width:295px;height:55px">Name</div>
  <div class="field" style="left:831px;top:3209px;width:296px;height:55px">Email Address</div>
  <div class="field" style="left:525px;top:3277px;width:295px;height:54px">Phone No</div>
  <div class="field" style="left:831px;top:3277px;width:296px;height:54px">Subject</div>
  <div class="field" style="left:525px;top:3345px;width:602px;height:155px">Message</div>
  <div class="btn btn--dark" style="left:525px;top:3512px;width:295px;height:54px">SUBMIT NOW</div>
</section>

<footer class="footer">
  <div class="footer__brand">REACH CRAFTERS</div>
  <p class="footer__copy">© Copyright © 2026 Company Name.<br>All Right Reserved</p>
  <span class="social" style="left:74px" role="img" aria-label="Social link"></span>
  <span class="social" style="left:105px" role="img" aria-label="Social link"></span>
  <span class="social" style="left:139px" role="img" aria-label="Social link"></span>
  <span class="social" style="left:179px" role="img" aria-label="Social link"></span>
  <span class="social" style="left:221px" role="img" aria-label="Social link"></span>

  <div class="footer__col" style="left:405px">
    <h4>QUICK LINKS</h4>
    <ul><li>Home</li><li>About Us</li><li>Services</li><li>Insights</li><li>Contact Us</li></ul>
  </div>
  <div class="footer__col" style="left:653px">
    <h4>SERVICES</h4>
    <ul><li>Nemo enim ipsam</li><li>Voluptatem</li><li>Quia voluptas sit</li><li>Aspernatur aut</li><li>Odit aut fugit</li></ul>
  </div>
  <div class="footer__col" style="left:933px">
    <h4>SUPPORT</h4>
    <ul><li>Nemo enim ipsam</li><li>Voluptatem</li><li>Quia voluptas sit</li><li>Aspernatur aut</li><li>Odit aut fugit</li></ul>
  </div>
</footer>

</body>
</html>
```